Visitenkarten/Briefpaier/Kassenkassenbelege für Juwelier
Zielgruppe
Mittelständischer Juwelier mit zwei Filialen. Klassischer Schmuck, Uhren und Modeschmuck
Aufgabenstellung
Es müssen für zwei Geschäfte Visitenkarten, Briefpapier (A4) und Kassenkassenbelege (A6) erstellt werden. Logo und Typo im Anhang. Ein Farbkonzept besteht noch nicht. Die Idee geht in Richtung Bordeaux-Rot.
Generell:
(1) Sieht erstmal nach viel Beschreibung aus, bitte nicht entmutigen lassen, sind zu 90% nur austauschbare Inhalts-/Kontaktdaten.
(2) Für meine Zwecke reicht es vollkommen aus, wenn bei den Vorschlägen zur Arbeitsersparnis erstmal nur mit einer Adresse gearbeitet wird. Wenn ich dann den zutreffenden Designvorschlag gefunden habe, können wir die zweite Adresse in dem ersten Format umsetzen. Ich denke das spart Zeit und Nerven.
(3) Bitte Angaben wie "Tel.:" oder "USt.- ID:" nicht wörtlich nehmen, es soll dabei klar sein worum es geht; wenn "Telefon" ausgeschrieben besser aussieht, bitte in der optisch ansprechenderen Form verwenden.
(4) Bei Fragen, bitte fragen!
(5) Viel Spass bei dem Projekt - Ich freu' mich auf die Vorschläge!
Visitenkarten(1):
Juwelier Brenneck GmbH
www.juwelier-brenneck-beispiel.de
Visitenkarten(2):
Visitenkarten(generell):
(1) Die einzelnen Daten können durch Hervorhebungen wie Adresse, Kontakt, Online/Internet unterteilt bzw. hervorgehoben werden.
(2) Die Visitenkarten sollen farbig gedruckt werden; geplant ist weiß als Hintergrund ist aber nicht zwingend bei einer guten anderen Idee
Briefpapier:
(1)Absender im Adressfeld für DIN-lang Briefumschläge mit Fenster:
(2)Informationen im Footer/Seitenbereich:
Juwelier Brenneck Gmb..

```html
<!DOCTYPE html>
<html lang="de">
<head>
<meta charset="utf-8">
<title>Juwelier Brenneck – Geschäftsausstattung</title>
<link href="https://fonts.googleapis.com/css2?family=Source+Sans+3:wght@400;600;700&display=swap" rel="stylesheet">
<style>
:root{
  --stage:#6a7784;
  --bordeaux:#6e2734;
  --bordeaux-soft:#9b5d63;
  --paper:#ffffff;
  --ink:#6b7580;
  --rule:#c9ccd0;
}
*{margin:0;padding:0;box-sizing:border-box}
html,body{width:1200px;height:1135px;overflow:hidden}
body{background:var(--stage);font-family:"Source Sans 3",sans-serif;color:var(--ink);position:relative}
.sheet{position:absolute;background:var(--bordeaux)}
.sheet-inner{position:absolute;background:var(--paper);overflow:hidden}
.abs{position:absolute}
.tab{position:absolute;background:var(--bordeaux)}
.brand{position:absolute;transform:translateX(-50%);white-space:nowrap;font-weight:700;color:var(--bordeaux);letter-spacing:.02em;text-transform:uppercase}
.bold{font-weight:600;color:var(--bordeaux)}
.gap{margin-top:.45em}
.fold{position:absolute;left:0;width:13px;height:1px;background:var(--rule)}

/* letterhead */
.letterhead{left:65px;top:86px;width:681px;height:963px}
.letterhead .sheet-inner{left:9px;top:9px;right:9px;bottom:9px}
.sender-line{left:65px;top:155px;font-size:6px;white-space:nowrap}
.sender-line b{font-weight:600}
.contact-block{left:490px;top:181px;border-left:1.3px solid var(--bordeaux);padding:2px 0 2px 15px;font-size:8.6px;line-height:1.36}
.footer{left:65px;top:907px;display:flex;font-size:8.2px;line-height:1.4}
.footer div{padding:0 14px;border-left:1.3px solid var(--bordeaux)}
.footer div:first-child{padding-left:0;border-left:none}

/* receipt */
.receipt{left:786px;top:86px;width:341px;height:480px}
.receipt .sheet-inner{left:7px;top:7px;right:7px;bottom:7px}
.receipt-contact{left:192px;top:13px;font-size:7.4px;line-height:1.32}
.receipt-note{left:18px;top:442px;font-size:7.4px;line-height:1.35;letter-spacing:.05em;color:var(--bordeaux)}

/* cards */
.card-dark{left:786px;top:621px;width:276px;height:175px;background:var(--bordeaux-soft)}
.card-dark .sheet-inner{left:7px;top:7px;right:7px;bottom:7px;background:var(--bordeaux)}
.card-dark .tab{background:var(--bordeaux-soft)}
.card-dark .brand{color:var(--paper)}
.card-light{left:786px;top:811px;width:276px;height:175px}
.card-light .sheet-inner{left:7px;top:7px;right:7px;bottom:7px}
.card-col{font-size:8px;line-height:1.4}
.card-col.right{font-size:7.6px}
</style>
</head>
<body>

<section class="sheet letterhead" aria-label="Briefpapier A4">
  <div class="sheet-inner">
    <div class="tab" style="left:304px;top:0;width:38px;height:70px"></div>
    <div class="brand" style="left:323px;top:84px;font-size:19px">Juwelier Brenneck</div>
    <p class="abs sender-line"><b>Juwelier Brenneck GmbH</b> | Goldschmiedeweg 12 | 45000 Musterstadt</p>
    <address class="abs contact-block" style="font-style:normal">
      <div class="bold">Juwelier Brenneck GmbH</div>
      <div>Goldschmiedeweg 12</div>
      <div>45000 Musterstadt</div>
      <div class="gap">Tel.:&nbsp; 0201 555120</div>
      <div>Fax:&nbsp; 0201 555129</div>
      <div class="gap">info@juwelier-brenneck-beispiel.de</div>
      <div>www.juwelier-brenneck-beispiel.de</div>
    </address>
    <span class="fold" style="top:332px"></span>
    <span class="fold" style="top:472px"></span>
    <span class="fold" style="top:672px"></span>
    <div class="abs footer">
      <div>Amtsgericht Musterstadt HRB 00000<br>Geschäftsführer: Helene Brenneck</div>
      <div>Steuernummer: 000/0000/0000<br>USt.- ID: DE 000123456</div>
      <div>Bankverbindung:<br>Musterbank AG Musterstadt</div>
      <div>IBAN: DE00 0000 0000 0000 0000 00<br>BIC: MUST DE 00</div>
    </div>
  </div>
</section>

<section class="sheet receipt" aria-label="Kassenbeleg A6">
  <div class="sheet-inner">
    <div class="tab" style="left:79px;top:0;width:28px;height:52px"></div>
    <div class="brand" style="left:93px;top:62px;font-size:13px">Juwelier Brenneck</div>
    <address class="abs receipt-contact" style="font-style:normal">
      <div class="bold">Juwelier Brenneck GmbH</div>
      <div>Goldschmiedeweg 12</div>
      <div>45000 Musterstadt</div>
      <div class="gap">Tel.:&nbsp; 0201 555120</div>
      <div>Fax:&nbsp; 0201 555129</div>
      <div class="gap">info@juwelier-brenneck-beispiel.de</div>
      <div>www.juwelier-brenneck-beispiel.de</div>
      <div class="gap">USt.- ID: DE 000123456</div>
    </address>
    <p class="abs receipt-note">Bei Umtausch oder Reklamation bitte Beleg vorlegen.<br>Barauszahlung ganz oder teilweise ausgeschlossen.</p>
  </div>
</section>

<section class="sheet card-dark" aria-label="Visitenkarte Vorderseite">
  <div class="sheet-inner">
    <div class="tab" style="left:113px;top:0;width:37px;height:64px"></div>
    <div class="brand" style="left:131px;top:80px;font-size:17px">Juwelier Brenneck</div>
  </div>
</section>

<section class="sheet card-light" aria-label="Visitenkarte Rückseite">
  <div class="sheet-inner">
    <div class="tab" style="left:113px;top:0;width:31px;height:42px"></div>
    <div class="brand" style="left:131px;top:52px;font-size:12.5px">Juwelier Brenneck</div>
    <div class="abs card-col" style="left:16px;top:100px">
      <div class="bold">Juwelier Brenneck GmbH</div>
      <div>Goldschmiedeweg 12</div>
      <div>45000 Musterstadt</div>
    </div>
    <div class="abs card-col right" style="left:132px;top:100px">
      <div>Tel.:&nbsp; 0201 555120</div>
      <div>Fax:&nbsp; 0201 555129</div>
      <div class="gap">info@juwelier-brenneck-beispiel.de</div>
      <div>www.juwelier-brenneck-beispiel.de</div>
    </div>
  </div>
</section>

</body>
</html>
```